Quick and easy spring book cover needed

We need a creative book cover design for a spring fiction book. The title of the book is The Lantern Harbor Theory. The author's name is Marcus Whitfield. The book is 4.25 x 7 inch. The spine is .5 inch. It should include the title, the author's name, and the emblem. The emblem should be set at .5 inches in length.
The book summary is as follows:
When Miriam Tolley moves from her homeland in Japan to pursue her dream as an editor in the United States, she soon encounters a young Washingtonian artist. After being given the task to interview him, she becomes fixated on the mystique surrounding his past. She conjures her inner detective skills to embark on, what she thinks is, the biggest story of her career. But will her heart get in her way?
The final design should reflect spring and young love, nothing sexual and overly romantic. The background and font colors should go well with the imagery. I have attached 2 photos in which should be incorporated. The third attachment is the emblem that is to be placed at the bottom of the spine.
Project Deadline Extended
Reason: The deadline has been extended to allow for revisions, in addition the publisher is considering multiple covers for this project.
Detective

```html
<!DOCTYPE html>
<html lang="en">
<head>
<meta charset="utf-8">
<title>The Lantern Harbor Theory — Book Cover</title>
<link href="https://fonts.googleapis.com/css2?family=Sancreek&family=Cinzel:wght@400;600&family=Oswald:wght@400&family=PT+Sans:ital,wght@1,700&display=swap" rel="stylesheet">
<style>
  :root {
    --paper: #ffffff;
    --magenta: #a0215f;
    --magenta-deep: #7d1648;
    --cream: #f7efc8;
    --plum-text: #5b1e6c;
    --grass: #6f8f3c;
    --bark: #5e4d3a;
    --foliage: #9cab7e;
    --blossom: #f4eef0;
    --spine-line: #d9d4d6;
  }
  * { box-sizing: border-box; margin: 0; padding: 0; }
  html, body { width: 1200px; height: 933px; overflow: hidden; background: var(--paper); }
  .cover { position: relative; width: 1200px; height: 933px; background: var(--paper); }

  /* Back cover */
  .back { position: absolute; left: 0; top: 0; width: 565px; height: 933px; }
  .back-photo {
    position: absolute; left: 0; top: 290px; width: 565px; height: 643px;
    background:
      linear-gradient(180deg, var(--paper) 0%, rgba(255,255,255,0.6) 22%, rgba(255,255,255,0) 45%),
      radial-gradient(ellipse 30% 60% at 45% 60%, var(--bark) 0%, rgba(94,77,58,0.6) 50%, rgba(94,77,58,0) 100%),
      linear-gradient(180deg, var(--foliage) 0%, #7f9260 55%, var(--grass) 80%, #5b6e35 100%);
  }
  .back-title {
    position: absolute; left: 74px; top: 58px; width: 220px; text-align: center;
    color: var(--magenta);
  }
  .back-title .small { font-family: "Cinzel", serif; font-size: 9px; font-weight: 600; letter-spacing: 1px; display: block; }
  .back-title .main {
    font-family: "Sancreek", cursive; font-size: 24px; line-height: 1; display: block;
    color: var(--magenta);
    text-shadow: -1px -1px 0 var(--cream), 1px -1px 0 var(--cream), -1px 1px 0 var(--cream), 1px 1px 0 var(--cream), 2px 3px 3px rgba(0,0,0,0.25);
  }
  .blurb {
    position: absolute; left: 78px; top: 176px; width: 462px;
    font-family: "PT Sans", sans-serif; font-style: italic; font-weight: 700;
    font-size: 13.4px; line-height: 29px; color: var(--plum-text);
  }

  /* Spine */
  .spine {
    position: absolute; left: 565px; top: 0; width: 46px; height: 933px;
    border-left: 1px solid var(--spine-line); border-right: 1px solid var(--spine-line);
    display: flex; flex-direction: column; align-items: center;
  }
  .imprint { margin-top: 26px; display: flex; flex-direction: column; align-items: center; gap: 3px; }
  .imprint .mark { width: 12px; height: 12px; background: var(--magenta); }
  .imprint .name { font-family: "Cinzel", serif; font-size: 6px; color: var(--magenta); letter-spacing: 0.5px; }
  .spine-author {
    margin-top: 48px; writing-mode: vertical-rl;
    font-family: "Cinzel", serif; font-size: 16px; letter-spacing: 9px; color: var(--magenta);
  }
  .spine-title {
    margin-top: 118px; writing-mode: vertical-rl;
    font-family: "Oswald", sans-serif; font-size: 26px; color: var(--magenta); letter-spacing: 0.5px;
  }

  /* Front cover */
  .front { position: absolute; left: 611px; top: 0; width: 589px; height: 933px; }
  .front-photo {
    position: absolute; left: 0; top: 390px; width: 589px; height: 543px;
    background:
      linear-gradient(180deg, var(--paper) 0%, rgba(255,255,255,0.4) 20%, rgba(255,255,255,0) 40%),
      radial-gradient(ellipse 35% 45% at 95% 70%, var(--blossom) 0%, rgba(244,238,240,0.7) 55%, rgba(244,238,240,0) 100%),
      radial-gradient(ellipse 30% 30% at 8% 35%, var(--blossom) 0%, rgba(244,238,240,0) 100%),
      linear-gradient(180deg, #c9d0d4 0%, #a9b5b8 30%, var(--grass) 55%, #4f7a2b 100%);
  }
  .front-title { position: absolute; left: 0; top: 126px; width: 589px; text-align: center; color: var(--magenta); }
  .front-title .small { display: block; font-family: "Cinzel", serif; font-weight: 600; font-size: 17px; letter-spacing: 2px; }
  .front-title .main {
    display: block; font-family: "Sancreek", cursive; font-size: 52px; line-height: 1.15;
    text-shadow: -2px -2px 0 var(--cream), 2px -2px 0 var(--cream), -2px 2px 0 var(--cream), 2px 2px 0 var(--cream), 4px 6px 6px rgba(0,0,0,0.3);
  }
  .front-author {
    position: absolute; left: 0; top: 887px; width: 589px; text-align: center;
    font-family: "Cinzel", serif; font-size: 15px; letter-spacing: 8px; color: var(--paper);
    text-shadow: 0 1px 3px rgba(0,0,0,0.4);
  }
</style>
</head>
<body>
<div class="cover">
  <section class="back">
    <div class="back-photo" role="img" aria-label="Photo of a young couple leaning against a large old tree trunk in a spring park"></div>
    <div class="back-title">
      <span class="small">THE</span>
      <span class="main">Lantern Harbor</span>
      <span class="small">THEORY</span>
    </div>
    <p class="blurb">When Miriam Tolley moves from her homeland in Japan to pursue her dream as an editor in the United States, she soon encounters a young Washingtonian artist. After being given the task to interview him, she becomes fixated on the mystique surrounding his past. She conjures her inner detective skills to embark on, what she thinks is, the biggest story of her career. But will her heart get in her way?</p>
  </section>

  <section class="spine">
    <div class="imprint">
      <span class="mark"></span>
      <span class="name">KESTREL</span>
    </div>
    <div class="spine-author">MARCUS WHITFIELD</div>
    <div class="spine-title">The Lantern Harbor Theory</div>
  </section>

  <section class="front">
    <div class="front-photo" role="img" aria-label="Photo of a young couple sitting on the grass under blossoming trees by the water"></div>
    <h1 class="front-title">
      <span class="small">THE</span>
      <span class="main">Lantern Harbor</span>
      <span class="small">THEORY</span>
    </h1>
    <div class="front-author">MARCUS WHITFIELD</div>
  </section>
</div>
</body>
</html>
```